Förderverein einer Kirchengemeinde sucht Flyer-Design
Zielgruppe
Wir sind ein Förderverein einer Kirchengemeinde, der sich für die kirchenmusikalische Arbeit einsetzt.
Wir wünschen uns ein niveauvolles und zeitgemäßes/modernes Flyerdesign, das die etablierten Konzertbesucher anspricht, aber vor allem auch Menschen erreicht und überzeugt, die (noch) nichts mit Kirche zu tun haben.
Das Alter der (Haupt-) Zielgruppe (Männer und Frauen) erstreckt sich von 45 bis 70 Jahren.
Aufgabenstellung
Bei der Wahl des Formates würden wir (aus der Sicht von Laien) ein zweimal gefaltetes DIN A4 quer Format nehmen. Aber wir lassen uns gerne überraschen und sind grundsätzlich für andere Lösungen offen.
Bitte den Abschnitt für Adress- und sonstige Dateneintragungen samt Kontodaten so gestalten und platzieren, dass man ihn leicht abtrennen und verschicken kann.
Der Flyer soll Kirchenmusik als lebendig und attraktiv darstellen und neue (jüngere) Mitglieder für den Freundeskreis werben.
Lassen Sie die Bilder sprechen!!

```html
<!DOCTYPE html>
<html lang="de">
<head>
<meta charset="utf-8">
<title>Freundeskreis Kirchenmusik – Flyer</title>
<link href="https://fonts.googleapis.com/css2?family=Nunito+Sans:ital,wght@0,400;0,600;0,700;1,400&display=swap" rel="stylesheet">
<style>
:root{
  --bg:#dcdcdc;
  --red:#b8161c;
  --red-dark:#8f1016;
  --red-light:#c81f25;
  --ink:#4a4a4a;
  --line:#b5b5b5;
  --bar:#d6d6d6;
  --white:#fff;
}
*{margin:0;padding:0;box-sizing:border-box}
html,body{width:1200px;height:954px;overflow:hidden;background:var(--bg)}
body{font-family:"Nunito Sans",Arial,sans-serif;color:var(--ink);position:relative}
.spread{position:absolute;left:39px;width:1134px;height:400px;background:var(--white);box-shadow:2px 3px 5px rgba(0,0,0,.35);overflow:hidden}
.spread--outside{top:44px}
.spread--inside{top:491px}
.panel{position:absolute;top:0;height:400px}
.photo{position:absolute}

/* form panel */
.form{left:0;width:339px}
.form__title{position:absolute;left:17px;top:10px;font-size:12.5px;font-weight:700;color:var(--red)}
.cell{position:absolute;border:1px solid var(--line);font-size:6.8px;padding:2px 3px;line-height:1.2}
.cell--noborder{border:none}
.rule{position:absolute;height:1px;background:var(--line)}
.bar{position:absolute;left:17px;width:310px;height:15px;background:var(--bar);font-size:8.3px;font-weight:700;padding:2px 3px}
.check{position:absolute;font-size:7.5px;display:flex;align-items:center;gap:3px;white-space:nowrap}
.check::before{content:"";width:6px;height:6px;border:1px solid #777;display:inline-block}
.note{position:absolute;font-size:6.6px;font-style:italic}
.bank{position:absolute;left:17px;top:346px;font-size:6.6px;line-height:10.6px}
.bank b{font-size:8.5px;font-weight:600;position:absolute;left:0;top:0}
.bank div{margin-left:66px}
.cutline{position:absolute;left:340px;top:0;height:400px;border-left:1px dashed #555}
.cutlabel{position:absolute;left:330px;top:390px;transform:rotate(-90deg);transform-origin:left top;font-size:4.5px;color:#777;white-space:nowrap}

/* contact panel */
.contact{left:343px;width:224px;background:var(--red)}
.contact__photo{left:0;top:0;width:224px;height:200px;background:linear-gradient(180deg,#cfc9bd 0%,#9b8a6a 30%,#a7a9ad 55%,#7e2a25 80%,#5c5a55 100%)}
.contact__brand{position:absolute;left:24px;top:216px;width:180px;display:flex;align-items:center;gap:6px;font-size:8.8px;font-weight:700;color:var(--white);letter-spacing:.2px}
.contact__brand i{width:7px;height:7px;background:var(--white);display:inline-block}
.contact__text{position:absolute;left:24px;top:245px;width:190px;font-size:8.6px;line-height:10.8px;color:var(--white)}
.contact__address{position:absolute;left:48px;top:295px;font-size:9.4px;line-height:11.5px;font-weight:700;color:var(--white)}
.contact__more{position:absolute;left:24px;top:357px;font-size:8.6px;line-height:12px;color:var(--white)}
.contact__more b{font-size:9.4px}

/* cover panel */
.cover{left:567px;width:567px}
.cover__photo{inset:0;background:linear-gradient(100deg,#8a6a2a 0%,#c9a24a 14%,#9a9a98 32%,#d8d8d4 48%,#5f5d58 62%,#b48a36 78%,#3b332a 100%)}
.cover__red{position:absolute;inset:0;background:linear-gradient(160deg,var(--red-dark),var(--red-light));clip-path:polygon(455px 0,567px 0,567px 400px,363px 400px)}
.cover__claim{position:absolute;left:80px;top:153px;font-size:19.5px;font-weight:600;color:var(--white);letter-spacing:.2px}
.cover__name{position:absolute;left:400px;width:160px;top:313px;text-align:center;font-size:16.5px;line-height:19.5px;font-weight:700;color:var(--white);letter-spacing:.4px}

/* inside left */
.groups{left:0;width:567px}
.groups__photos{position:absolute;inset:0;clip-path:polygon(0 0,151px 0,243px 400px,0 400px)}
.groups__recorder{left:0;top:0;width:260px;height:120px;background:linear-gradient(180deg,#6b8a4e,#8b8a7a 60%,#6f7a55)}
.groups__children{left:0;top:120px;width:260px;height:112px;background:linear-gradient(180deg,#3f6b32,#cdb648 55%,#7a8f5a)}
.groups__brass{left:0;top:232px;width:260px;height:168px;background:linear-gradient(180deg,#c9c8c2,#e8e6e0 45%,#8e8a80)}
.groups__heading{position:absolute;right:248px;top:47px;text-align:right;font-size:17px;line-height:19.5px;font-weight:700;color:var(--red)}
.groups__divider{position:absolute;left:327px;top:46px;width:1px;height:84px;background:var(--red)}
.groups__intro{position:absolute;left:337px;top:48px;width:200px;font-size:10px;line-height:14px}
.groups__intro p+p{margin-top:9px}
.groups__sub{position:absolute;left:219px;top:159px;font-size:12.5px;font-weight:700;color:var(--red)}
.benefit{position:absolute;font-size:9.5px;line-height:12.6px;width:290px}
.benefit span{display:block;padding-left:13px}

/* inside right */
.reasons{left:567px;width:567px;background:linear-gradient(160deg,var(--red-dark),var(--red-light))}
.reasons__photos{position:absolute;inset:0;clip-path:polygon(0 0,252px 0,341px 400px,0 400px)}
.reasons__choir{left:0;top:0;width:345px;height:185px;background:linear-gradient(180deg,#c8bfae,#a08a6a 35%,#2a2622 60%,#1c1a18)}
.reasons__organist{left:0;top:185px;width:345px;height:215px;background:linear-gradient(150deg,#e8d6a8,#b88a44 40%,#2a241d 70%,#141210)}
.reasons__heading{position:absolute;left:284px;top:49px;font-size:14px;font-weight:700;color:var(--white)}
.reasons__intro{position:absolute;left:294px;top:78px;font-size:10px;color:var(--white)}
.reason{position:absolute;font-size:9.6px;line-height:12.4px;color:var(--white);width:230px}
.reason span{display:block;padding-left:14px}
</style>
</head>
<body>

<section class="spread spread--outside">
  <div class="panel form">
    <h2 class="form__title">Beitrittserklärung</h2>
    <div class="cell" style="left:17px;top:33px;width:310px;height:15px">Name, Vorname</div>
    <div class="cell" style="left:17px;top:47px;width:310px;height:15px">für die Institution/Firma + persönlich</div>
    <div class="cell" style="left:17px;top:61px;width:310px;height:30px">Straße, Hausnr., PLZ, Ort</div>
    <div class="rule" style="left:20px;top:76px;width:302px"></div>
    <div class="cell" style="left:17px;top:90px;width:154px;height:15px">Telefon/Handy</div>
    <div class="cell" style="left:170px;top:90px;width:157px;height:15px">Geburtstag</div>
    <div class="cell" style="left:17px;top:104px;width:154px;height:29px">Emailadresse</div>
    <div class="cell" style="left:170px;top:104px;width:157px;height:29px">Datum, Unterschrift</div>
    <div class="rule" style="left:20px;top:128px;width:146px"></div>
    <div class="rule" style="left:175px;top:128px;width:148px"></div>

    <div class="bar" style="top:145px">Mitgliedsbeiträge</div>
    <div class="check" style="left:20px;top:165px">Einzelpersonen € 20,-</div>
    <div class="check" style="left:20px;top:176px">Ehepaare/Partnerschaften € 32,-</div>
    <div class="check" style="left:20px;top:188px">Institutionen/Firmen € 95,-</div>
    <div class="note" style="left:28px;top:200px">(jeweils Mindestbeiträge)</div>
    <div class="check" style="left:165px;top:165px">Frei wählbarer Betrag : €</div>
    <div class="rule" style="left:263px;top:175px;width:62px"></div>
    <div class="check" style="left:165px;top:180px">Ich benötige eine Spendenbescheinigung</div>
    <div class="check" style="left:165px;top:194px">Einmalige Spende <i>&nbsp;(ohne Mitgliedschaft)</i></div>

    <div class="bar" style="top:220px">SEPA-Lastschriftmandat</div>
    <div class="cell" style="left:17px;top:234px;width:186px;height:20px;padding-top:5px">IBAN</div>
    <div class="cell" style="left:202px;top:234px;width:125px;height:20px;padding-top:5px">BIC</div>
    <div class="cell" style="left:17px;top:253px;width:154px;height:21px;padding-top:6px">Kreditinstitut</div>
    <div class="cell" style="left:170px;top:253px;width:157px;height:21px;padding-top:6px">Kontoinhaber</div>
    <div class="cell" style="left:17px;top:273px;width:310px;height:47px;padding-top:5px">Hiermit ermächtige ich den Freundeskreis Kirchenmusik den von mir zu entrichtenden<br>Mitgliedsbeitrag von meinem Konto einzuziehen<br><span style="display:block;margin-top:8px">Ort, Datum, Unterschrift</span></div>
    <div class="rule" style="left:111px;top:313px;width:208px"></div>
    <div class="cell" style="left:17px;top:319px;width:310px;height:17px;padding-top:4px;font-style:italic">Der Einzug der Mitgliedsbeiträge erfolgt zu Beginn eines Kalenderjahres</div>

    <div class="bank">
      <b>Spendenkonto:</b>
      <div>Sparkasse Wendrode-Aller</div>
      <div>IBAN: DE 00 1234 5678 9012 3456 78</div>
      <div>BIC: SPKADE21WND</div>
      <div>Verwendungszweck bei Einzelspenden unter Angabe der Kostenstelle …</div>
    </div>
  </div>
  <div class="cutline"></div>
  <div class="cutlabel">Hier abtrennen</div>

  <div class="panel contact">
    <div class="photo contact__photo" role="img" aria-label="Barocke Orgel mit goldverzierten Pfeifentürmen"></div>
    <div class="contact__brand">FREUNDESKREIS <i></i> KIRCHENMUSIK</div>
    <p class="contact__text">Wenn Sie die Kirchenmusik an St. Laurentius als Mitglied im <b>Freundeskreis Kirchenmusik</b> fördern möchten, senden Sie die ausgefüllte Beitrittserklärung an den</p>
    <p class="contact__address">Freundeskreis Kirchenmusik,<br>Kirchengemeinde St. Laurentius,<br>Lindenweg 7, 31234 Wendrode,<br>Tel.: 05120-447210,<br>hanna.leiter@kirchenpost.de</p>
    <p class="contact__more">Nähere Informationen finden Sie unter<br><b>www.kirchenmusik-wendrode.de</b></p>
  </div>

  <div class="panel cover">
    <div class="photo cover__photo" role="img" aria-label="Nahaufnahme silberner Orgelpfeifen mit goldenem Schnitzwerk"></div>
    <div class="cover__red"></div>
    <h1 class="cover__claim">Kirchenmusik braucht Freunde…</h1>
    <p class="cover__name">FREUNDESKREIS<br>KIRCHENMUSIK</p>
  </div>
</section>

<section class="spread spread--inside">
  <div class="panel groups">
    <div class="groups__photos">
      <div class="photo groups__recorder" role="img" aria-label="Flötenensemble mit Blockflöten im Garten"></div>
      <div class="photo groups__children" role="img" aria-label="Kinderchor in gelben T-Shirts im Grünen"></div>
      <div class="photo groups__brass" role="img" aria-label="Posaunenchor mit Blechblasinstrumenten vor einem Gebäude"></div>
    </div>
    <h2 class="groups__heading">Kirchenmusik<br>braucht Freunde</h2>
    <div class="groups__divider"></div>
    <div class="groups__intro">
      <p>Im Jahr 1999 gegründet, unterstützt der Freundeskreis Kirchenmusik die vielfältigen musikalischen Aktivitäten an der St. Laurentius-Kirche.</p>
      <p>Wir laden Sie ein, Mitglied zu werden!</p>
    </div>
    <h3 class="groups__sub">Mit Ihrem Beitrag …</h3>
    <p class="benefit" style="left:224px;top:184px">…bereichern Sie Wendrodes kulturelle Landschaft durch den Erhalt<span>und Ausbau unseres hohen kirchenmusikalischen Niveaus</span></p>
    <p class="benefit" style="left:231px;top:218px">…stärken Sie das Ehrenamt</p>
    <p class="benefit" style="left:236px;top:239px">…ermöglichen Sie der Kantorei, dem Posaunenchor, dem<span>Kinderchor und dem Flötenensemble regelmäßige Proben-</span><span>arbeit, Probenwochenenden und die Anschaffung von</span><span style="padding-left:18px">Notenmaterial</span></p>
    <p class="benefit" style="left:249px;top:297px">…erhalten Sie die historische Johann Brenner Orgel von 1748</p>
    <p class="benefit" style="left:254px;top:318px">…fördern Sie die Ausbildung kirchenmusikalischen Nach-<span>wuchses</span></p>
  </div>

  <div class="panel reasons">
    <div class="reasons__photos">
      <div class="photo reasons__choir" role="img" aria-label="Kantorei singt in der Kirche vor dem Barockaltar"></div>
      <div class="photo reasons__organist" role="img" aria-label="Hände auf der Klaviatur eines Orgelspieltischs"></div>
    </div>
    <h2 class="reasons__heading">Mitglieder haben gute Gründe:</h2>
    <p class="reasons__intro">Sie…</p>
    <p class="reason" style="left:300px;top:96px">… erhalten ermäßigte Eintrittspreise von<span>gemeindeeigenen Konzerten</span></p>
    <p class="reason" style="left:310px;top:133px">… können Konzertkarten vor dem öffentlichen<span>Verkauf erwerben</span></p>
    <p class="reason" style="left:318px;top:170px">… gestalten die Arbeit des Freundeskreises<span>in den jährlichen Mitgliederversammlungen</span><span style="padding-left:18px">aktiv mit</span></p>
    <p class="reason" style="left:331px;top:220px">… erhalten aktuelle Informationen über<span>Veranstaltungen der Gemeinde bequem</span><span>per Email und profitieren so zu allererst</span></p>
    <p class="reason" style="left:343px;top:269px">… können den Mitgliedsbeitrag steuerlich<span>absetzen und erhalten eine Spenden-</span><span style="padding-left:17px">bescheinigung</span></p>
    <p class="reason" style="left:355px;top:319px">… können an Ausflügen des<span>Freundeskreises teilnehmen</span></p>
  </div>
</section>

</body>
</html>
```